New Business Card Design Project

I need a design for business cards, i am an electrical business called "Corvane Electrical and Communications" i need the cards to be double sided with the company logo on the back (attached) the front needs to say my company name, web site, email address, telephone number, and ABN number and electrical license number. I am open to different arrangements of the information but would like the background to be incorporating something electrical or something that looks smart. open to all additional ideas also.

The company colours are orange and grey see logo attached.

Business Name: Corvane Electrical and Communications
Website: corvaneelectricalandcomms.example.com.au
Email: brent@corvaneelectricalandcomms.example.com.au
Telephone(mobile): 0481209736
ABN: 71208349162
Lic No: 418273D

Target Market(s)

Business entities, Project Managers, Accounts, Clients

Industry/Entity Type

Electrician

Contact Information for Business Card

I need a design for business cards, i am an electrical business called "Corvane Electrical and Communications" i need the cards to be double sided with the company logo on the back (attached) the front needs to say my company name

Font styles to use
Serif
Sans Serif

Colors
f37122
5c5c5c

Requirements
Must have
• Must have the Logo on the back open to different ways of it being on the back but had in mind to keep it central but again open to other options
Nice to have
• A real modern cool background that is eye catching yet contemporary
Should not have
• No backgrounds of a light bulb or plug or anything like that

```html
<!DOCTYPE html>
<html lang="en">
<head>
<meta charset="utf-8">
<title>Corvane Electrical and Communications – Business Card</title>
<link rel="stylesheet" href="https://fonts.googleapis.com/css2?family=Arimo:wght@400;700&family=Exo+2:wght@500;700&display=swap">
<style>
  :root {
    --orange: #f37122;
    --grey: #5c5c5c;
    --charcoal-dark: #232323;
    --charcoal-light: #4d4d4d;
    --frost-top: #f1efec;
    --frost-bottom: #dedbd7;
    --ink: #3a3a3a;
    --ink-soft: #4a4a4a;
    --backdrop: #e9e8e6;
  }
  html, body {
    margin: 0;
    padding: 0;
    width: 1200px;
    height: 969px;
    overflow: hidden;
    background: var(--backdrop);
  }
  .canvas {
    position: relative;
    width: 1200px;
    height: 969px;
  }
  .card {
    position: absolute;
    left: 120px;
    top: 212px;
    width: 960px;
    height: 545px;
    border-radius: 30px;
    overflow: hidden;
    box-shadow: 0 18px 40px rgba(0,0,0,0.18);
    font-family: "Arimo", Arial, sans-serif;
  }
  .card-art {
    position: absolute;
    inset: 0;
    width: 960px;
    height: 545px;
    display: block;
  }
  .brand {
    position: absolute;
    left: 0;
    right: 0;
    top: 128px;
    text-align: center;
  }
  .brand-name {
    display: inline-flex;
    align-items: center;
    gap: 14px;
    font-family: "Exo 2", Arial, sans-serif;
    font-weight: 500;
    font-size: 31px;
    letter-spacing: 1px;
    color: var(--orange);
    margin-left: 50px;
  }
  .brand-dot {
    width: 16px;
    height: 16px;
    border-radius: 50%;
    background: var(--orange);
  }
  .details {
    position: absolute;
    left: 45px;
    top: 328px;
    margin: 0;
    padding: 0;
    list-style: none;
    color: var(--ink-soft);
  }
  .details li {
    line-height: 1;
    white-space: nowrap;
  }
  .details .reg {
    font-size: 26px;
    margin-bottom: 9px;
    color: var(--grey);
  }
  .details .mobile {
    font-size: 27px;
    margin-top: 15px;
    margin-bottom: 12px;
    color: var(--ink);
  }
  .details .mobile .label {
    color: var(--orange);
    font-weight: 700;
  }
  .details .web {
    font-size: 22px;
    margin-bottom: 14px;
    color: var(--ink);
  }
  .person {
    position: absolute;
    right: 52px;
    top: 410px;
    text-align: right;
    font-family: "Exo 2", Arial, sans-serif;
    font-weight: 700;
    line-height: 1;
  }
  .person-name {
    font-size: 34px;
    color: var(--orange);
    margin: 0 0 10px;
  }
  .person-role {
    font-size: 27px;
    color: #2b2b2b;
    margin: 0;
  }
</style>
</head>
<body>
<main class="canvas">
  <article class="card">
    <svg class="card-art" viewBox="0 0 960 545" aria-hidden="true">
      <defs>
        <linearGradient id="frost" x1="0" y1="0" x2="0" y2="1">
          <stop offset="0" stop-color="var(--frost-top)"/>
          <stop offset="1" stop-color="var(--frost-bottom)"/>
        </linearGradient>
        <linearGradient id="band" x1="0" y1="0" x2="1" y2="0.6">
          <stop offset="0" stop-color="var(--charcoal-dark)"/>
          <stop offset="0.55" stop-color="#2f2f2f"/>
          <stop offset="1" stop-color="var(--charcoal-light)"/>
        </linearGradient>
      </defs>
      <rect class="card-frost" width="960" height="545" fill="url(#frost)"/>
      <path class="card-band" d="M0 0 H960 V322 C640 312 300 270 0 202 Z" fill="url(#band)"/>
      <path class="card-swoosh-shadow" d="M0 209 C300 277 640 318 960 328" fill="none" stroke="#2a2a2a" stroke-width="3" opacity="0.5"/>
      <path class="card-swoosh" d="M0 204 C300 272 640 313 960 323" fill="none" stroke="var(--orange)" stroke-width="6"/>
    </svg>

    <div class="brand">
      <span class="brand-name"><span class="brand-dot"></span>CORVANE ELECTRICAL &amp; COMMUNICATIONS</span>
    </div>

    <ul class="details">
      <li class="reg">ABN: 71208349162</li>
      <li class="reg">Lic No: 418273D</li>
      <li class="mobile"><span class="label">Mobile :</span> 0481209736</li>
      <li class="web">brent@corvaneelectricalandcomms.example.com.au</li>
      <li class="web">corvaneelectricalandcomms.example.com.au</li>
    </ul>

    <div class="person">
      <p class="person-name">Brent Harlow</p>
      <p class="person-role">CEO/Founder</p>
    </div>
  </article>
</main>
</body>
</html>
```